Now Leasing Banner

Looking for a banner that says the following information approx 4' x 30'

Now Leasing Maplebrook Terrace 925-318-6042

Target Market(s)

Drive by traffic

Industry/Entity Type

Residential property management

Requirements
Must have
• Clear and readable from a distance

```html
<!DOCTYPE html>
<html lang="en">
<head>
<meta charset="utf-8">
<title>Now Leasing Banner – Maplebrook Terrace</title>
<link rel="stylesheet" href="https://fonts.googleapis.com/css2?family=Oswald:wght@700&family=Open+Sans:wght@800&display=swap">
<style>
  :root {
    --page-bg: #f3f3f3;
    --banner-navy: #27205f;
    --text-white: #ffffff;
    --accent-blue: #1ba3e6;
    --photo-light: #f4f4f5;
    --photo-mid: #cfd2d8;
    --photo-warm: #b9724f;
  }
  html, body {
    margin: 0;
    width: 1200px;
    height: 662px;
    overflow: hidden;
    background: var(--page-bg);
  }
  .canvas {
    position: relative;
    width: 1200px;
    height: 662px;
    display: flex;
    align-items: center;
    justify-content: center;
  }
  .banner {
    width: 1120px;
    height: 148px;
    display: block;
    box-shadow: 6px 10px 14px rgba(0, 0, 0, 0.25);
  }
  .banner-bg { fill: var(--banner-navy); }
  .headline {
    font-family: "Oswald", "Arial Narrow", sans-serif;
    font-weight: 700;
    fill: var(--text-white);
  }
  .property-name,
  .phone-number {
    font-family: "Open Sans", Arial, sans-serif;
    font-weight: 800;
    fill: var(--text-white);
  }
  .photo-divider {
    fill: none;
    stroke: var(--accent-blue);
    stroke-width: 3;
  }
</style>
</head>
<body>
<main class="canvas">
  <svg class="banner" viewBox="0 0 1120 148" xmlns="http://www.w3.org/2000/svg" aria-label="Now Leasing Maplebrook Terrace 925-318-6042">
    <defs>
      <linearGradient id="photoTone" x1="0" y1="0" x2="1" y2="0">
        <stop offset="0" stop-color="var(--photo-light)"/>
        <stop offset="0.45" stop-color="var(--photo-mid)"/>
        <stop offset="0.8" stop-color="#dcdde1"/>
        <stop offset="1" stop-color="var(--photo-warm)"/>
      </linearGradient>
      <linearGradient id="edgeGlow" x1="0" y1="0" x2="1" y2="0">
        <stop offset="0" stop-color="#ffffff" stop-opacity="0"/>
        <stop offset="1" stop-color="#ffffff" stop-opacity="0.35"/>
      </linearGradient>
    </defs>

    <rect class="banner-bg" x="0" y="0" width="1120" height="148"/>

    <g class="banner-headline">
      <text class="headline now-word" font-size="40" transform="translate(57 131) rotate(-90)" textLength="116" lengthAdjust="spacingAndGlyphs">NOW</text>
      <text class="headline leasing-word" x="66" y="133" font-size="148" textLength="435" lengthAdjust="spacingAndGlyphs">LEASING</text>
    </g>

    <g class="banner-contact">
      <text class="property-name" x="520" y="62" font-size="46" textLength="348" lengthAdjust="spacingAndGlyphs">Maplebrook Terrace</text>
      <text class="phone-number" x="517" y="127" font-size="64" textLength="352" lengthAdjust="spacingAndGlyphs">925-318-6042</text>
    </g>

    <path d="M878 0 Q860 74 881 148 L893 148 Q873 74 920 0 Z" fill="url(#edgeGlow)"/>
    <path class="banner-photo" role="img" aria-label="Photo of a hand holding a house-shaped key in front of a blurred apartment building"
          d="M920 0 L1120 0 L1120 148 L923 148 Q873 74 920 0 Z" fill="url(#photoTone)"/>
    <path class="photo-divider" d="M920 0 Q873 74 923 148"/>
  </svg>
</main>
</body>
</html>
```